Management Consultancy needs sharp professional services showcased in a brochure

We are a management consultancy specializing on contract management and conflict avoidance services requiring a professional brochure showcasing our services to prospective clients.

Attached are a selection of existing stationary and the colour scheme.

Further details on our company can be found at www.velt-advisory-partners.com
Updates

Preference is for bi-fold, however, innovative tri-fold will be considered. Added Monday, August 7, 2017

Target Market(s)

Construction companies, consultants, developers, oil and gas service providers, NGO's, SME's.

Industry/Entity Type

Management

Requirements
Must have
• High degree of professionalism with eye catching, sharp detail. No frils.
• Colour scheme as per the attachments
• Font as per attachments - Century Gothic
• Details of our company and services
Nice to have
• Open to ideas, thinking along the lines of a car brochure type design.
• Bi-fold preferred, by trifold accepted if innovative.
Should not have
• Remove reference to the United Arab Emirates.
• No cartoon/clipart photos.

```html
<!DOCTYPE html>
<html lang="en">
<head>
<meta charset="utf-8">
<title>Velt Advisory – Bi-fold Brochure</title>
<link href="https://fonts.googleapis.com/css2?family=Questrial&family=Montserrat:wght@600;700&display=swap" rel="stylesheet">
<style>
  :root{
    --bg:#e6e6e8;
    --red:#8e1b26;
    --red-deep:#6e1119;
    --red-bright:#a3222e;
    --navy:#1f2a48;
    --navy-soft:#2c3a5e;
    --white:#ffffff;
    --ink:#3a3f4d;
    --photo-light:#e9ecef;
    --photo-mid:#c9ced6;
  }
  *{box-sizing:border-box;margin:0;padding:0}
  html,body{width:1200px;height:789px;overflow:hidden;background:var(--bg)}
  body{font-family:"Questrial",sans-serif;position:relative}
  .spread{position:absolute;left:105px;top:45px;width:990px;height:700px;display:flex;box-shadow:0 6px 24px rgba(0,0,0,.18)}
  .page{position:relative;width:495px;height:700px;overflow:hidden}

  /* back page */
  .page--back{background:linear-gradient(160deg,var(--red-bright) 0%,var(--red) 45%,var(--red-deep) 100%);color:var(--white)}
  .page--back .deco{position:absolute;inset:0}
  .about{position:absolute;left:42px;top:58px;width:400px}
  .about__title{font-family:"Montserrat",sans-serif;font-weight:700;font-size:19px;letter-spacing:.5px;padding-bottom:8px;border-bottom:1px solid rgba(255,255,255,.45);margin-bottom:10px}
  .about__title span{font-family:"Questrial",sans-serif;font-weight:400}
  .about p{font-size:8.6px;line-height:1.45;margin-bottom:9px;color:rgba(255,255,255,.92)}
  .about p.lead{font-size:12px;line-height:1.3}
  .about ul{list-style:none;margin:-3px 0 9px}
  .about li{font-family:"Montserrat",sans-serif;font-weight:600;font-size:9px;line-height:1.6;padding-left:14px;position:relative}
  .about li::before{content:"";position:absolute;left:0;top:4px;width:6px;height:6px;border:1.4px solid var(--white);transform:rotate(45deg)}
  .about .quote{font-family:"Montserrat",sans-serif;font-weight:700;font-size:10px;line-height:1.4;color:var(--white)}
  .back-brand{position:absolute;left:42px;bottom:70px}
  .brand-name{font-family:"Questrial",sans-serif;font-size:26px;letter-spacing:1.5px;text-transform:uppercase;display:flex;align-items:center;gap:10px}
  .brand-name .dot{width:14px;height:14px;border-radius:50%;background:currentColor;display:inline-block}
  .back-brand .brand-name{color:var(--white)}
  .contact{position:absolute;left:42px;bottom:28px;font-size:10px;line-height:1.7;color:var(--white)}
  .contact div{display:flex;align-items:center;gap:8px}
  .contact svg{width:11px;height:11px}

  /* front page */
  .page--front{background:var(--white)}
  .page--front svg.cover{position:absolute;inset:0}
  .front-brand{position:absolute;right:40px;bottom:95px}
  .front-brand .brand-name{color:var(--navy);font-size:28px}
  .front-url{position:absolute;left:190px;bottom:36px;font-size:10px;color:var(--ink);padding-bottom:5px;border-bottom:2px solid var(--red)}
</style>
</head>
<body>
  <div class="spread">
    <section class="page page--back">
      <svg class="deco" viewBox="0 0 495 700" preserveAspectRatio="none" aria-hidden="true">
        <path d="M495 440 C450 510 420 600 418 700 L495 700 Z" fill="var(--navy)" opacity=".85"/>
        <path d="M0 560 C120 600 250 640 330 700 L0 700 Z" fill="var(--red-deep)" opacity=".6"/>
      </svg>
      <div class="about">
        <h2 class="about__title">ABOUT <span>US</span></h2>
        <p class="lead">We are an experienced contract and conflict advisory providing global contract performance solutions and conflict management to:</p>
        <ul>
          <li>International Development Organisations;</li>
          <li>Construction Industry;</li>
          <li>Oil And Gas Industry; And</li>
          <li>Government Sectors.</li>
        </ul>
        <p>Observing the standard of consultancy services and magnitude of contractual engagements and conflicts, we see the opportunity to make things better: better engagements, better awareness, better performance, which all lead to better value in terms of financial benefit and relationship maintenance. We firmly believe in party success in a non litigious environment.</p>
        <p>Our services are uniquely delivered through our integrated management consultancy model, with a single point of contact and responsibility, and focused attention to detail. We provide advisory services and solutions resolving past and current claims, and in doing so, preparing our clients for a conflict free future based on our core principles of integrity, equality and strength, ensuring compliance and experience at an intimate professional level. We aim to have our clients feel our principles in our presence and in our advisories, giving the service which is deserved.</p>
        <p class="lead">Our clients range from leading multinational companies, international contractors to government bodies and authorities.</p>
        <p>Velt Advisory is more than just a professional advisory consultancy; we are an integrated professional team with deep domain expertise, industry knowledge and the ability to work across multiple jurisdictions supported by a wide professional network.</p>
        <p>We forge strong client partnerships and in doing so, we develop and maintain these relationships through performance and delivery of professional services which create and maximise value for our clients.</p>
        <p>Through our unique approach to contract and conflict management, we want the best for our clients to ensure that contract integrity, compliance and performance is maintained with the upmost faith, based around our principles.</p>
        <p class="quote">"If value, whether financial or relationship is not achieved, then we are not finished, we have only just begun."</p>
      </div>
      <div class="back-brand"><div class="brand-name"><span class="dot"></span>Velt Advisory</div></div>
      <div class="contact">
        <div><svg viewBox="0 0 12 12"><rect x="1" y="2.5" width="10" height="7" fill="none" stroke="#fff"/><path d="M1 2.5 L6 6.5 L11 2.5" fill="none" stroke="#fff"/></svg>jmarlow@velt-advisory-partners.com</div>
        <div><svg viewBox="0 0 12 12"><circle cx="6" cy="6" r="5" fill="none" stroke="#fff"/><ellipse cx="6" cy="6" rx="2.2" ry="5" fill="none" stroke="#fff"/><path d="M1 6 H11" stroke="#fff"/></svg>www.velt-advisory-partners.com</div>
      </div>
    </section>

    <section class="page page--front">
      <svg class="cover" viewBox="0 0 495 700" preserveAspectRatio="none">
        <defs>
          <linearGradient id="photoTone" x1="0" y1="0" x2="1" y2="1">
            <stop offset="0" stop-color="var(--photo-light)"/>
            <stop offset=".6" stop-color="var(--photo-mid)"/>
            <stop offset="1" stop-color="#aeb5c0"/>
          </linearGradient>
        </defs>
        <rect x="0" y="0" width="495" height="700" fill="url(#photoTone)" role="img" aria-label="Photograph of business people meeting around a glass conference table"/>
        <path d="M40 0 L140 0 C200 120 330 210 495 250 L495 290 C300 270 130 170 40 0 Z" fill="var(--red)" opacity=".88"/>
        <path d="M0 40 C60 150 80 330 40 700 L0 700 Z" fill="var(--navy-soft)" opacity=".8"/>
        <path d="M55 700 C85 520 250 390 495 360 L495 700 Z" fill="var(--navy)"/>
        <path d="M115 700 C150 570 290 470 495 450 L495 700 Z" fill="var(--white)"/>
      </svg>
      <div class="front-brand"><div class="brand-name"><span class="dot"></span>Velt Advisory</div></div>
      <div class="front-url">www.velt-advisory-partners.com</div>
    </section>
  </div>
</body>
</html>
```